Stationary Set Rebrand for Brennick

We are a Canadian Distribution and Service Company that was established in 1969. Over the past 5 decades we have expanded our business and have warehouses across Canada. We specialize in adhesive tapes, adhesives, films, safety, warehouse, shipping, janitorial and packaging supplies.

We have updated our logo design and would like a new corporate branding identity that includes a new fresh Stationary Set (Business Cards, Letterhead, Letterhead MS Word, Envelope, Presentation Folders, Email Signatures, Notepad Covers, etc.)

Target Market(s)

Industrial Business Sector

Font styles to use
Sans Serif

Colors
0054AA
0677BA
7BADD7
CADEEF
E8F1F8
0094D4
00A9DD
6FCCEA
C7EBF8
E9F6FB
00AB8E
00BBA5
67D7C9
C6EFE9
E9F9F6
EB3D1F
EC4F4E
F09395
F8D3D4
FCEDEE

Requirements
Should not have
• Colors not too light, darker colours preferred

```html
<!DOCTYPE html>
<html lang="en">
<head>
<meta charset="utf-8">
<title>Brennick Business Card</title>
<link href="https://fonts.googleapis.com/css2?family=Open+Sans:wght@400;600;700;800&display=swap" rel="stylesheet">
<style>
  :root {
    --stage: #2a2a2c;
    --card-white: #ffffff;
    --card-dark: #1f1f20;
    --ink: #1c1c1c;
    --grey: #555555;
    --red: #d81920;
    --white: #ffffff;
  }
  * { margin: 0; padding: 0; box-sizing: border-box; }
  html, body {
    width: 1200px; height: 900px; overflow: hidden;
    background: var(--stage);
    font-family: "Open Sans", Arial, sans-serif;
  }
  .stage {
    position: relative; width: 1200px; height: 900px;
  }
  .card {
    position: absolute; left: 250px; width: 700px; height: 400px;
    overflow: hidden; box-shadow: 0 12px 30px rgba(0,0,0,.45);
  }
  .card--front { top: 40px; background: var(--card-white); }
  .card--back { top: 470px; background: var(--card-dark); }

  .card-art { position: absolute; inset: 0; }

  .wordmark {
    font-weight: 800; letter-spacing: -1px; line-height: 1;
  }
  .tagline {
    font-weight: 700; font-size: 13px; letter-spacing: .2px;
  }

  .front-brand { position: absolute; left: 44px; top: 38px; color: var(--ink); }
  .front-brand .wordmark { font-size: 58px; }
  .front-brand .tagline { margin-top: 4px; }

  .contact { position: absolute; left: 44px; top: 150px; color: var(--grey); }
  .contact-name {
    color: var(--red); font-weight: 700; font-size: 22px;
    text-transform: uppercase; letter-spacing: .5px;
  }
  .contact-role { font-size: 17px; margin-bottom: 16px; }
  .contact-address { font-size: 17px; line-height: 1.3; margin-bottom: 14px; }
  .contact-list { list-style: none; font-size: 17px; line-height: 1.5; }
  .contact-list li { display: flex; align-items: center; gap: 8px; }
  .contact-icon { width: 16px; height: 16px; flex: none; }

  .back-brand {
    position: absolute; left: 0; right: 0; top: 120px;
    text-align: center; color: var(--white);
  }
  .back-brand .wordmark-row {
    display: inline-flex; align-items: center; gap: 14px;
  }
  .back-brand .wordmark { font-size: 96px; }
  .brand-dot { width: 18px; height: 18px; background: var(--red); }
  .back-brand .tagline { font-size: 18px; margin-top: 8px; }
</style>
</head>
<body>
<main class="stage">

  <section class="card card--front">
    <svg class="card-art" width="700" height="400" viewBox="0 0 700 400">
      <path d="M282 400 C 410 330 550 130 628 0 L700 0 L700 400 Z" fill="var(--red)"/>
      <path d="M296 400 C 424 330 562 130 640 0 L700 0 L700 400 Z" fill="var(--card-dark)" stroke="var(--white)" stroke-width="4"/>
      <circle cx="470" cy="245" r="120" fill="var(--red)" stroke="var(--white)" stroke-width="5" role="img" aria-label="Large brand symbol"/>
    </svg>

    <div class="front-brand">
      <div class="wordmark">Brennick</div>
      <div class="tagline">Tape and Packaging Specialists</div>
    </div>

    <div class="contact">
      <div class="contact-name">Marcus Hale</div>
      <div class="contact-role">Managing Director</div>
      <div class="contact-address">Your Address, City<br>State, Zip 0000</div>
      <ul class="contact-list">
        <li>
          <svg class="contact-icon" viewBox="0 0 16 16"><path d="M3 2 L6 2 L7 5 L5.5 6.5 C6.5 8.5 7.5 9.5 9.5 10.5 L11 9 L14 10 L14 13 C14 13.6 13.6 14 13 14 C7 14 2 9 2 3 C2 2.4 2.4 2 3 2 Z" fill="var(--red)"/></svg>
          044-555 018 240
        </li>
        <li>
          <svg class="contact-icon" viewBox="0 0 16 16"><rect x="1" y="3" width="14" height="10" rx="1" fill="var(--red)"/><path d="M1.5 3.5 L8 9 L14.5 3.5" fill="none" stroke="var(--white)" stroke-width="1.3"/></svg>
          hello@brennick.ca
        </li>
        <li>
          <svg class="contact-icon" viewBox="0 0 16 16"><circle cx="8" cy="8" r="7" fill="var(--red)"/><path d="M1 8 H15 M8 1 C5 4 5 12 8 15 M8 1 C11 4 11 12 8 15" fill="none" stroke="var(--white)" stroke-width="1"/></svg>
          www.brennick.ca
        </li>
      </ul>
    </div>
  </section>

  <section class="card card--back">
    <div class="back-brand">
      <div class="wordmark-row">
        <span class="wordmark">Brennick</span>
        <span class="brand-dot"></span>
      </div>
      <div class="tagline">Tape and Packaging Specialists</div>
    </div>
  </section>

</main>
</body>
</html>
```